Merrow Trade finance web design

We are a newly established business which provides invoice finance to Small Businesses in England and Wales.
Our approach is very much a funder where the small business owner can talk to the decision maker. We will guarantee on receipt of information, a decision within 24 hours.
We are not a bank so the look of the website need to be friendly but professional.
Have two types of people we are trying to attract to the website: 1) partners who are small business owners and 2) introducers who is accountants and commercial brokers who introduce us to the small businesses.
Currently no website, although domain has been reserved.
The design should be:
Professional
“Clean” Look
Designed to convey Trust and Authority.
Appeal to the small business owner.
Must incorporate:
Logo (attached)
Front page:Top tabs to other pages 1) About us 2) Services 3) Introducers 4) Contact us
Need picture and logo on page.
1) About us page- Room for talk about the company, the people and our critera.
2) Services page- We need for what invoice finance is, and 5 boxes for different services we will provide. (link on page to contact us)
3) Introducers page- We need a part for why become an introducer? Who we can help? Why we are different? (link on page to contact us)
4) Contact us page- Office address, email, tel and if possible a map and a contact me part which will email direct to us.
Text will be provided for the design, if we can see the setup of the website we will provide a part for each of the pages to support.
Styles we think convey the correct image:
www.dornelcapital.example
www.plivanlend.example
www.quorbacredit.example
Target Market(s)
Small business owners
Industry/Entity Type
Finance
Number of Pages Required
5+ page
Look and feel

```html
<!DOCTYPE html>
<html lang="en">
<head>
<meta charset="utf-8">
<title>Merrow Trade finance</title>
<link rel="stylesheet" href="https://fonts.googleapis.com/css2?family=Raleway:wght@300;400;500;600;700&family=Open+Sans:ital,wght@0,400;0,600;1,400&display=swap">
<style>
:root{
  --red:#c10f1d;
  --red-dark:#9a0a14;
  --grey-mid:#808080;
  --grey-light:#c6c6c6;
  --panel:#f0f0f0;
  --text:#333;
  --muted:#a3a3a3;
  --footer:#111111;
  --footer-bar:#1f1f1f;
  --white:#ffffff;
}
*{margin:0;padding:0;box-sizing:border-box}
html,body{width:1200px;height:2667px;overflow:hidden;background:var(--white)}
body{position:relative;font-family:"Open Sans",Arial,sans-serif;color:var(--text)}
.abs{position:absolute}

/* header */
.site-header{position:absolute;left:0;top:0;width:1200px;height:96px;background:var(--white)}
.brand{position:absolute;left:128px;top:22px;display:flex;align-items:center;gap:10px;font-family:"Raleway",sans-serif;font-weight:700;font-size:42px;color:var(--red);line-height:1}
.brand-dot{width:14px;height:14px;border-radius:50%;background:var(--red)}
.main-nav a{position:absolute;top:38px;font-family:"Raleway",sans-serif;font-size:15.5px;font-weight:500;color:#222;text-decoration:none;letter-spacing:.2px}
.main-nav a.active{color:var(--red)}
.main-nav a.active::after{content:"";position:absolute;left:-6px;right:-6px;top:56px;height:3px;background:var(--red)}

/* hero */
.hero{position:absolute;left:0;top:96px;width:1200px;height:519px;background:linear-gradient(100deg,#5b5048 0%,#7a6e66 35%,#8d8580 60%,#6b6862 100%)}
.hero-shade{position:absolute;inset:0;background:rgba(30,25,22,.35)}
.hero-title{position:absolute;left:0;width:1200px;top:134px;text-align:center;font-family:"Raleway",sans-serif;font-weight:400;font-size:40px;line-height:50px;color:var(--white)}
.hero-sub{position:absolute;left:280px;width:640px;top:238px;text-align:center;font-size:16px;line-height:24px;color:#e8e4e0}
.btn-outline{position:absolute;left:523px;top:306px;width:153px;height:37px;border:2px solid var(--white);color:var(--white);font-family:"Raleway",sans-serif;font-weight:600;font-size:14.5px;display:flex;align-items:center;justify-content:center;letter-spacing:.4px}
.hero-dots{position:absolute;left:565px;top:485px;display:flex;gap:5px}
.hero-dots span{width:15px;height:15px;border-radius:50%;background:var(--white)}
.hero-dots span.current{background:transparent;border:2px solid var(--white)}

/* service cards */
.service-card{position:absolute;top:672px;width:302px;height:295px;text-align:center;color:var(--white);border-bottom:4px solid rgba(0,0,0,.2)}
.service-card.red{background:var(--red);left:132px}
.service-card.grey{background:var(--grey-mid);left:450px}
.service-card.light{background:var(--grey-light);left:768px}
.service-card svg{position:absolute;left:111px;top:36px}
.service-card h3{position:absolute;left:0;right:0;top:128px;font-family:"Raleway",sans-serif;font-weight:500;font-size:22px}
.service-card p{position:absolute;left:30px;right:30px;top:164px;font-size:12.5px;line-height:20px;color:rgba(255,255,255,.85)}
.service-card .btn{position:absolute;left:89px;top:222px;width:124px;height:37px;display:flex;align-items:center;justify-content:center;font-family:"Raleway",sans-serif;font-weight:700;font-size:13px;color:var(--white)}
.red .btn{background:var(--red-dark)}
.grey .btn{background:#5e5e5e}
.light .btn{background:#a9a9a9}

/* about */
.about{position:absolute;left:0;top:1026px;width:1200px;height:442px;background:var(--panel);border-top:1px solid #e2e2e2;border-bottom:1px solid #e2e2e2}
.section-title{font-family:"Raleway",sans-serif;font-weight:400;font-size:34px;color:#333}
.body-copy{font-size:13.5px;line-height:24px;color:var(--muted)}
.btn-solid{background:var(--red-dark);color:var(--white);font-family:"Raleway",sans-serif;font-weight:700;font-size:13px;display:flex;align-items:center;justify-content:center}
.invoice-preview{position:absolute;left:667px;top:76px;width:404px;height:290px;border:1px solid #ccc;background:linear-gradient(180deg,#e9e9e9 0 14px,#1f2b33 14px 82px,#f4f4f4 82px 100%)}

/* introducers */
.introducers{position:absolute;left:0;top:1468px;width:1200px;height:448px;background:var(--white)}
.intro-photo{position:absolute;left:0;top:0;width:711px;height:448px;background:linear-gradient(90deg,#c7bfb3 0%,#e3ddd3 45%,#f3f0ec 70%,rgba(255,255,255,0) 100%)}

/* testimonials */
.testimonials{position:absolute;left:0;top:1916px;width:1200px;height:404px;background:var(--red);color:var(--white)}
.testimonials h2{position:absolute;left:0;right:0;top:60px;text-align:center;font-family:"Raleway",sans-serif;font-weight:400;font-size:28px}
.quote{position:absolute;top:134px;width:301px;height:149px;border:2px solid rgba(255,255,255,.9);padding:26px 26px 0 30px;font-style:italic;font-size:12.5px;line-height:22px}
.quote::after{content:"";position:absolute;left:30px;bottom:-11px;width:18px;height:18px;background:var(--red);border-right:2px solid rgba(255,255,255,.9);border-bottom:2px solid rgba(255,255,255,.9);transform:rotate(45deg)}
.author{position:absolute;top:302px;display:flex;align-items:center;gap:10px}
.avatar{width:44px;height:44px;border-radius:50%;background:#e6d2c4;border:2px solid #f2f2f2}
.author b{display:block;font-family:"Raleway",sans-serif;font-weight:500;font-size:15px}
.author small{display:block;font-size:11.5px;margin-top:2px}

/* footer */
.site-footer{position:absolute;left:0;top:2320px;width:1200px;height:288px;background:var(--footer)}
.footer-col{position:absolute;top:62px}
.footer-col h4{font-family:"Raleway",sans-serif;font-weight:400;font-size:21px;color:#eee;margin-bottom:16px}
.footer-col a{display:block;font-size:14px;line-height:28px;color:#bdbdbd;text-decoration:none}
.social a{display:flex;align-items:center;gap:14px;line-height:34px}
.social i{width:14px;height:14px;border-radius:50%;background:#eee;display:inline-block}
.footer-bar{position:absolute;left:0;top:2608px;width:1200px;height:59px;background:var(--footer-bar);color:#9a9a9a;font-size:12px;display:flex;align-items:center;justify-content:center}
</style>
</head>
<body>

<header class="site-header">
  <div class="brand"><span class="brand-dot"></span>Merrow</div>
  <nav class="main-nav">
    <a class="active" href="#" style="left:409px">HOME</a>
    <a href="#" style="left:489px">ABOUT US</a>
    <a href="#" style="left:601px">SERVICES</a>
    <a href="#" style="left:706px">INTRODUCERS</a>
    <a href="#" style="left:848px">CLIENTS</a>
    <a href="#" style="left:946px">CONTACT US</a>
  </nav>
</header>

<section class="hero">
  <div class="abs" style="inset:0" role="img" aria-label="Photo of a smiling couple on a sofa reviewing paperwork"></div>
  <div class="hero-shade"></div>
  <h1 class="hero-title">We Provide Invoice Finance Services<br>to Small Businesses</h1>
  <p class="hero-sub">Aommodo a mi Morbi ornare gravida elit Integer congue augue et malesuada iaculis ipsum dui aliquet felis at cursus magna nisl nec elit Praesent</p>
  <a class="btn-outline">GET A QUOTE</a>
  <div class="hero-dots"><span class="current"></span><span></span><span></span><span></span></div>
</section>

<section class="services">
  <div class="service-card red">
    <svg width="80" height="80" viewBox="0 0 80 80" fill="none" stroke="#fff" stroke-width="3">
      <path d="M22 8h30l12 12v52H22z"/><path d="M52 8v12h12"/>
      <path d="M16 14v64h42"/>
      <path d="M44 34h14M44 44h14M44 54h14M44 64h14"/>
      <text x="26" y="58" fill="#fff" stroke="none" font-family="Raleway,sans-serif" font-size="26" font-weight="700">$</text>
    </svg>
    <h3>Invoice Finance</h3>
    <p>commodo a mi Morbi ornare gravida elit Integer congue augue et males</p>
    <a class="btn">READ MORE</a>
  </div>
  <div class="service-card grey">
    <svg width="80" height="80" viewBox="0 0 80 80" fill="none" stroke="#fff" stroke-width="3">
      <rect x="4" y="10" width="72" height="48"/><path d="M32 58l-4 12h24l-4-12M22 70h36"/>
      <path d="M12 48v-8M19 48v-14M26 48v-10M33 48v-18" stroke-width="4"/>
      <path d="M12 34l8-8 7 5 10-11"/>
      <circle cx="56" cy="34" r="13" fill="#fff"/><path d="M56 34V21M56 34l11 7" stroke="#808080"/>
    </svg>
    <h3>Finance Managment</h3>
    <p>commodo a mi Morbi ornare gravida elit Integer congue augue et males</p>
    <a class="btn">READ MORE</a>
  </div>
  <div class="service-card light">
    <svg width="80" height="80" viewBox="0 0 80 80" fill="none" stroke="#fff" stroke-width="3">
      <circle cx="40" cy="32" r="20"/><circle cx="40" cy="32" r="14"/>
      <path d="M30 52v12h20V52M30 58h20M34 70h12"/>
      <path d="M40 2v6M14 10l4 4M66 10l-4 4M8 32h5M67 32h5"/>
      <text x="34" y="39" fill="#fff" stroke="none" font-family="Raleway,sans-serif" font-size="18" font-weight="700">$</text>
    </svg>
    <h3>Consulting</h3>
    <p>commodo a mi Morbi ornare gravida elit Integer congue augue et males</p>
    <a class="btn">READ MORE</a>
  </div>
</section>

<section class="about">
  <h2 class="section-title abs" style="left:142px;top:80px">Merrow Trade finance</h2>
  <p class="body-copy abs" style="left:142px;top:134px;width:455px">Curabitur iaculis tempus eros Curabitur vel mi sit amet magna male-suada ultrices Ut nisi erat fermentum vel congue id euismod in elit Fusce ultricies orci ac feugiat suscipit leo massa</p>
  <p class="body-copy abs" style="left:142px;top:214px;width:455px">sodales velit et scelerisque mi tortor at ipsum cligula augue bibendum accumsan vestibulum ut commodo a mi Morbi</p>
  <a class="btn-solid abs" style="left:144px;top:286px;width:123px;height:36px">READ MORE</a>
  <div class="invoice-preview" role="img" aria-label="Screenshot of an invoice layout with service items and prices"></div>
</section>

<section class="introducers">
  <div class="intro-photo" role="img" aria-label="Photo of a woman on a sofa working through paperwork with a calculator and laptop"></div>
  <h2 class="section-title abs" style="left:604px;top:86px">Introducers</h2>
  <p class="body-copy abs" style="left:604px;top:140px;width:455px">Curabitur iaculis tempus eros Curabitur vel mi sit amet magna male-suada ultrices Ut nisi erat fermentum vel congue id euismod in elit Fusce ultricies orci ac feugiat suscipit leo massa</p>
  <p class="body-copy abs" style="left:604px;top:220px;width:455px">sodales velit et scelerisque mi tortor at ipsum cligula augue bibendum accumsan vestibulum ut commodo a mi Morbi</p>
  <a class="btn-solid abs" style="left:606px;top:288px;width:123px;height:36px">READ MORE</a>
</section>

<section class="testimonials">
  <h2>What People are Saying</h2>
  <blockquote class="quote" style="left:153px">“ Curabitur vel dolor ultrices ipsum dictum tristique Praesent vitae lacus Ut velit enim vestibulum non fermentum nec hendrerit quis leo Pellentesque rutrum ”</blockquote>
  <blockquote class="quote" style="left:471px">“ Duis non nunc Nulla rhoncus dictum metus Curabitur tristique mi condimentum orci Phasellus pellentesque aliquam enim Proin dui lectus cursus eu ”</blockquote>
  <blockquote class="quote" style="left:788px">“ Nam eget lacus Aliquam erat volutpat Quisque dignissim congue leo Mauris vel lacus vitae felis vestibulum volutpat Etiam est nunc venenatis in trist”</blockquote>
  <div class="author" style="left:160px"><span class="avatar" role="img" aria-label="Reviewer portrait"></span><div><b>By Author Name</b><small>City Location</small></div></div>
  <div class="author" style="left:478px"><span class="avatar" role="img" aria-label="Reviewer portrait"></span><div><b>By Author Name</b><small>City Location</small></div></div>
  <div class="author" style="left:797px"><span class="avatar" role="img" aria-label="Reviewer portrait"></span><div><b>By Author Name</b><small>City Location</small></div></div>
</section>

<footer class="site-footer">
  <div class="footer-col" style="left:153px"><h4>Quick Links</h4><a>About Us</a><a>Why Choose Us</a><a>Introducers</a></div>
  <div class="footer-col" style="left:340px"><h4>Services</h4><a>Nullam enim</a><a>Leo egestas</a><a>Condimentum</a><a>At laoreet</a></div>
  <div class="footer-col" style="left:532px"><h4>Resources</h4><a>Testimonials</a><a>Blogs</a><a>Our Clients</a></div>
  <div class="footer-col" style="left:715px"><h4>Need Help</h4><a>Request a Demo</a><a>Support</a><a>Contact Us</a></div>
  <div class="footer-col social" style="left:923px;top:54px"><h4>Social</h4><a><i></i>Friendloop</a><a><i></i>Chirpline</a><a><i></i>Plusboard</a><a><i></i>Vidstream</a></div>
</footer>
<div class="footer-bar">© 2016 Company Name &nbsp;All right reserved</div>

</body>
</html>
```